Venture 482 - Lumora Book Cover

I am looking for a Lumora book cover for my book about "Venture 482".
The Book is Titled:
Venture 482 Ascended
Shaping Outcomes: Paths To Unlocking Cosmic Truths
Author is Dorian Pell
Here is a book description that may help you understand more about it:
Inspired by the genius of Edwin Marlowe, this comprehensive guide delves into the ancient wisdom and cutting-edge science behind the 482 method, a powerful tool for manifesting your desires. Whether you're seeking personal growth, financial success, or spiritual enlightenment, this book provides advanced techniques and methods to transform your dreams into reality.
Any questions please ask.
Thanks
Owen

```html
<!DOCTYPE html>
<html lang="en">
<head>
<meta charset="utf-8">
<title>Venture 482 Ascended — Dorian Pell</title>
<link rel="stylesheet" href="https://fonts.googleapis.com/css2?family=Marcellus+SC&family=Poppins:wght@300;700;800&family=Tinos&display=swap">
<style>
  :root {
    --sky-top: #121c2e;
    --sky-mid: #2b3850;
    --dusk-glow: #c9606a;
    --dusk-deep: #6a3c55;
    --sea-top: #2a3a52;
    --sea-bottom: #0c1320;
    --cream: #f6e6da;
    --salmon: #d0625a;
    --white: #f4f6f8;
  }
  * { margin: 0; padding: 0; box-sizing: border-box; }
  html, body { width: 805px; height: 1200px; overflow: hidden; background: var(--sky-top); }
  .cover {
    position: relative;
    width: 805px;
    height: 1200px;
    overflow: hidden;
  }
  .cover-art {
    position: absolute;
    inset: 0;
    background:
      radial-gradient(ellipse 260px 420px at 400px 640px, rgba(230,240,245,0.55), rgba(60,160,150,0.25) 55%, transparent 80%),
      linear-gradient(180deg,
        var(--sky-top) 0%,
        var(--sky-mid) 30%,
        var(--dusk-deep) 45%,
        var(--dusk-glow) 56%,
        var(--dusk-deep) 66%,
        var(--sea-top) 72%,
        var(--sea-bottom) 100%);
  }
  .author {
    position: absolute;
    top: 78px;
    left: 0;
    width: 805px;
    text-align: center;
    padding-left: 24px;
    font-family: "Marcellus SC", serif;
    font-size: 50px;
    letter-spacing: 0.36em;
    color: var(--cream);
  }
  .title {
    position: absolute;
    top: 192px;
    left: 0;
    width: 805px;
    text-align: center;
    font-family: "Poppins", sans-serif;
  }
  .title-word {
    display: block;
    font-weight: 700;
    font-size: 84px;
    line-height: 1;
    letter-spacing: -0.01em;
    color: var(--cream);
    text-shadow: 0 3px 6px rgba(0,0,0,0.35);
  }
  .title-number {
    display: block;
    margin-top: -4px;
    font-weight: 800;
    font-size: 158px;
    line-height: 1;
    letter-spacing: -0.02em;
    color: var(--salmon);
    text-shadow: 0 4px 8px rgba(0,0,0,0.3);
  }
  .title-edition {
    display: block;
    margin-top: 8px;
    font-weight: 700;
    font-size: 40px;
    line-height: 1;
    letter-spacing: 0.34em;
    padding-left: 0.34em;
    color: var(--salmon);
  }
  .subtitle {
    position: absolute;
    top: 1030px;
    left: 0;
    width: 805px;
    text-align: center;
    color: var(--white);
  }
  .subtitle-lead {
    display: block;
    font-family: "Poppins", sans-serif;
    font-weight: 300;
    font-size: 31px;
    letter-spacing: 0.02em;
    line-height: 1.1;
  }
  .subtitle-rest {
    display: block;
    margin-top: 14px;
    font-family: "Tinos", serif;
    font-size: 27px;
    line-height: 1.32;
  }
</style>
</head>
<body>
  <main class="cover">
    <div class="cover-art" role="img" aria-label="Illustration: an open teal door standing on a rocky islet in a dark sea, clouds drifting through it, under a stormy dusk sky with a red glow on the horizon"></div>

    <p class="author">DORIAN PELL</p>

    <h1 class="title">
      <span class="title-word">VENTURE</span>
      <span class="title-number">482</span>
      <span class="title-edition">ASCENDED</span>
    </h1>

    <p class="subtitle">
      <span class="subtitle-lead">SHAPING OUTCOMES:</span>
      <span class="subtitle-rest">Paths to unlocking<br>cosmic truths</span>
    </p>
  </main>
</body>
</html>
```